Real Estate agent needs flyer/folder to contain bio and overview of services

I'm including files of the layout of the small folder. The folder is 6 1/2 across and 9 1/2 inches long. It will have a front & back cover and then writing on the 2 inside pages.

I am sending a few files to incorporate into the flyer, 1 new logo to use and 2 files which are coloring ideas.

Colors

Designer to choose colors to be used in the design.

```html
<!DOCTYPE html>
<html lang="en">
<head>
<meta charset="utf-8">
<title>Marissa Delcourt – Realtor Folder</title>
<link rel="stylesheet" href="https://fonts.googleapis.com/css2?family=Lora:ital,wght@0,400;0,500;0,700;1,400&family=Source+Sans+3:ital,wght@0,400;0,600;1,400&display=swap">
<style>
:root{
  --navy:#23428a;
  --blue:#2f55b0;
  --bright:#3a62b5;
  --soft:#a9b7da;
  --ink:#2b2b2b;
  --paper:#ffffff;
  --mist:#e6e7ec;
  --backdrop:#e9e9ec;
  --serif:'Lora', Georgia, serif;
  --sans:'Source Sans 3', Arial, sans-serif;
}
*{box-sizing:border-box;margin:0;padding:0}
html,body{width:837px;height:1200px;overflow:hidden}
body{background:var(--backdrop);position:relative;font-family:var(--sans);color:var(--ink)}

/* ---------- outer spread: back + front cover ---------- */
.outer-spread{position:absolute;left:81px;top:76px;width:690px;height:502px}
.outer-spread .shapes{position:absolute;inset:0}
.brand-standin{position:absolute;font-family:var(--sans);font-weight:600;letter-spacing:1px;color:var(--paper);text-align:center}
.back-cover .brand-standin{left:113px;top:278px;width:120px;font-size:11px}
.back-quote{position:absolute;left:43px;top:350px;width:260px;font-family:var(--serif);font-style:italic;font-size:11px;line-height:14px;color:var(--paper);text-align:center}
.cover-name{position:absolute;left:0;top:442px;width:345px;text-align:center;color:var(--paper);font-size:10.5px;font-weight:600;letter-spacing:.3px}
.contact-row{position:absolute;top:476px;height:12px;font-size:7.6px;color:var(--paper);display:flex;align-items:center}
.contact-row span{display:flex;align-items:center;gap:4px;position:absolute;white-space:nowrap}
.icon{width:9px;height:9px;flex:none}
.front-logo{position:absolute;left:395px;top:130px;width:250px;text-align:center;font-family:var(--serif);font-weight:500;font-size:27px;line-height:31px;letter-spacing:2px;color:var(--blue)}
.front-headline{position:absolute;left:345px;top:396px;width:340px;text-align:center;font-family:var(--serif);font-weight:700;font-size:20.5px;line-height:26px;color:var(--paper)}

/* ---------- inner spread ---------- */
.inner-spread{position:absolute;left:95px;top:620px;width:676px;height:502px}
.inner-spread .panel-bg{position:absolute;left:0;top:0}
.page-bg{position:absolute;top:0;height:502px}
.page-bg.middle{left:158px;width:172px;background:linear-gradient(90deg,#fff 0%,#fbfbfc 70%,#e4e5ea 100%)}
.page-bg.right{left:330px;width:346px;background:linear-gradient(90deg,#e8e9ee 0%,#fbfbfc 14%,#fff 30%)}
.hero-photo{position:absolute;left:158px;top:0;width:518px;height:171px;
  background:linear-gradient(180deg,#1d2740 0%,#3b3e4a 38%,#8a6a3e 62%,#4f7da6 82%,#2d5f8c 100%)}
.fold-line{position:absolute;left:0;top:0}

.agent-photo{position:absolute;left:26px;top:19px;width:106px;height:106px;border-radius:50%;border:3px solid var(--bright);
  background:radial-gradient(circle at 50% 40%,#e9d6bf 0%,#c8a985 45%,#8d7b6a 100%)}
.agent-id{position:absolute;left:0;top:140px;width:158px;text-align:center;color:var(--soft);line-height:1.25}
.agent-id .name{font-size:8.5px}
.agent-id .title{font-size:7px}
.agent-id .license{font-size:5.5px}
.intro-title{position:absolute;left:8px;top:184px;width:145px;text-align:center;font-family:var(--serif);font-size:10px;color:var(--paper)}
.intro-body{position:absolute;left:12px;top:208px;width:137px;color:var(--paper);font-size:6.4px;line-height:7.6px;text-align:justify}
.intro-body p{margin-bottom:6px}
.agent-contact{position:absolute;left:0;top:424px;width:149px;text-align:right;color:var(--paper)}
.agent-contact .name{font-size:11px;font-weight:600;letter-spacing:.3px;margin-bottom:8px}
.agent-contact .line{font-size:7.8px;line-height:14px;display:flex;justify-content:flex-end;align-items:center;gap:4px}

.inner-brand{left:565px;top:142px;width:100px;font-size:11px}

.column{position:absolute;font-size:6.5px;line-height:7.9px}
.column p{text-align:justify;margin-bottom:6px}
.column.middle{left:167px;top:186px;width:149px}
.column.right{left:349px;top:186px;width:307px}
.section-title{font-family:var(--serif);font-size:10px;color:var(--blue);margin-bottom:9px}
.column.right .section-title{text-align:center;margin-bottom:6px}
.tenet-lead{font-size:13px;color:var(--ink);margin:-2px 0 5px}
.section-title.spaced{margin-top:13px}

.testimonial{position:absolute;top:441px;height:48px;border:1px solid #7891cc;border-radius:4px;padding:9px 5px 3px;
  font-size:5px;line-height:6.1px;font-style:italic;color:#555;text-align:justify}
.testimonial .mark{position:absolute;top:-8px;left:50%;transform:translateX(-50%);background:var(--paper);padding:0 3px;
  font-family:var(--serif);font-weight:700;font-style:normal;font-size:15px;line-height:14px;color:var(--blue)}
.testimonial.one{left:167px;width:149px}
.testimonial.two{left:349px;width:136px}
.testimonial.three{left:490px;width:136px}
</style>
</head>
<body>

<section class="outer-spread" aria-label="Folder covers">
  <svg class="shapes" width="690" height="502" viewBox="0 0 690 502">
    <defs>
      <clipPath id="folder-edge"><path d="M0 0 H668 Q700 240 680 502 H0 Z"/></clipPath>
      <linearGradient id="dusk" x1="0" y1="0" x2="0" y2="1">
        <stop offset="0" stop-color="#7b8fb4"/>
        <stop offset=".45" stop-color="#8c7a62"/>
        <stop offset=".7" stop-color="#3c4457"/>
        <stop offset="1" stop-color="#1c2538"/>
      </linearGradient>
      <linearGradient id="sheen" x1="0" y1="0" x2="1" y2="1">
        <stop offset="0" stop-color="#ffffff"/>
        <stop offset=".6" stop-color="#f1f1f4"/>
        <stop offset="1" stop-color="#dcdde3"/>
      </linearGradient>
    </defs>
    <g clip-path="url(#folder-edge)">
      <rect x="0" y="0" width="345" height="502" fill="var(--navy)"/>
      <g role="img" aria-label="Photo of a modern poolside patio lounge at dusk">
        <polygon points="0,0 345,0 345,250 175,143 0,245" fill="url(#dusk)"/>
      </g>
      <polygon points="0,165 0,245 110,185" fill="#2d55a8"/>
      <rect x="345" y="0" width="345" height="502" fill="url(#sheen)"/>
      <polygon points="345,242 520,341 690,246 690,502 345,502" fill="var(--navy)"/>
      <polygon points="520,341 690,246 690,432" fill="var(--bright)"/>
    </g>
  </svg>

  <div class="back-cover">
    <div class="brand-standin">SUMMIT REALTY</div>
    <p class="back-quote">Along with being your Realtor, I’m a lifelong resource for all things home-related &amp; beyond…if you need a great referral for anything at all, call me! I can’t wait to work with you!</p>
    <div class="cover-name">MARISSA DELCOURT</div>
    <div class="contact-row">
      <span style="left:19px"><svg class="icon" viewBox="0 0 10 10"><circle cx="5" cy="5" r="4.4" fill="none" stroke="#fff" stroke-width=".8"/><ellipse cx="5" cy="5" rx="1.8" ry="3.2" fill="none" stroke="#fff" stroke-width=".6"/><line x1="1.8" y1="5" x2="8.2" y2="5" stroke="#fff" stroke-width=".6"/></svg>www.marissadhomes.com</span>
      <span style="left:141px"><svg class="icon" viewBox="0 0 10 10"><circle cx="5" cy="5" r="4.4" fill="none" stroke="#fff" stroke-width=".8"/><path d="M3.3 2.8 L4.2 2.6 L4.7 3.9 L4.1 4.4 Q4.7 5.6 5.7 6 L6.2 5.4 L7.4 5.9 L7.2 6.8 Q4 7 3.3 2.8 Z" fill="#fff"/></svg>555 013 2748</span>
      <span style="left:228px"><svg class="icon" viewBox="0 0 10 10"><circle cx="5" cy="5" r="4.4" fill="none" stroke="#fff" stroke-width=".8"/><rect x="2.7" y="3.4" width="4.6" height="3.2" fill="none" stroke="#fff" stroke-width=".6"/><path d="M2.7 3.4 L5 5.2 L7.3 3.4" fill="none" stroke="#fff" stroke-width=".6"/></svg>marissa@marissadhomes.com</span>
    </div>
  </div>

  <div class="front-cover">
    <div class="front-logo">MARISSA<br>DELCOURT</div>
    <h1 class="front-headline">Helping You<br>Make Better Decisions…</h1>
    <div class="contact-row">
      <span style="left:363px"><svg class="icon" viewBox="0 0 10 10"><circle cx="5" cy="5" r="4.4" fill="none" stroke="#fff" stroke-width=".8"/><ellipse cx="5" cy="5" rx="1.8" ry="3.2" fill="none" stroke="#fff" stroke-width=".6"/><line x1="1.8" y1="5" x2="8.2" y2="5" stroke="#fff" stroke-width=".6"/></svg>www.marissadhomes.com</span>
      <span style="left:478px"><svg class="icon" viewBox="0 0 10 10"><circle cx="5" cy="5" r="4.4" fill="none" stroke="#fff" stroke-width=".8"/><path d="M3.3 2.8 L4.2 2.6 L4.7 3.9 L4.1 4.4 Q4.7 5.6 5.7 6 L6.2 5.4 L7.4 5.9 L7.2 6.8 Q4 7 3.3 2.8 Z" fill="#fff"/></svg>555 013 2748</span>
      <span style="left:553px"><svg class="icon" viewBox="0 0 10 10"><circle cx="5" cy="5" r="4.4" fill="none" stroke="#fff" stroke-width=".8"/><rect x="2.7" y="3.4" width="4.6" height="3.2" fill="none" stroke="#fff" stroke-width=".6"/><path d="M2.7 3.4 L5 5.2 L7.3 3.4" fill="none" stroke="#fff" stroke-width=".6"/></svg>marissa@marissadhomes.com</span>
    </div>
  </div>
</section>

<section class="inner-spread" aria-label="Folder inside pages">
  <svg class="panel-bg" width="158" height="502" viewBox="0 0 158 502"><path d="M22 0 Q-16 251 22 502 H158 V0 Z" fill="var(--navy)"/></svg>
  <div class="page-bg middle"></div>
  <div class="page-bg right"></div>
  <div class="hero-photo" role="img" aria-label="Photo of a luxury home with lit pool and terrace at night"></div>
  <svg class="fold-line" width="676" height="502" viewBox="0 0 676 502"><path d="M627 0 Q700 250 627 500" fill="none" stroke="#555" stroke-width=".8" stroke-dasharray="3 3"/></svg>

  <div class="agent-photo" role="img" aria-label="Portrait photo of the agent"></div>
  <div class="agent-id">
    <div class="name">Marissa Delcourt</div>
    <div class="title">Realtor®</div>
    <div class="license">DRE# 01234567</div>
  </div>
  <h2 class="intro-title">Let me introduce myself</h2>
  <div class="intro-body">
    <p>I’m originally from Chicago, but I’m a full-fledged California girl now. I’ve lived and worked in Orange County since 1996. I always say where we live is the next best thing to living on a tropical island. I’ve traveled to many and I’m always happy to come back to my Laguna Niguel home.</p>
    <p>My passion for this area is why I’m in Real Estate. I consider myself incredibly fortunate to sell homes and help people purchase homes in an area that I love with all my heart.</p>
    <p>This passion also carries over in representing my clients with the highest degree of professionalism, enthusiasm and care. My business is built on exceptional customer service and I’m grateful my clients are mostly repeat and referrals.</p>
  </div>
  <div class="agent-contact">
    <div class="name">MARISSA DELCOURT</div>
    <div class="line">555 013 2748<svg class="icon" viewBox="0 0 10 10"><circle cx="5" cy="5" r="4.4" fill="none" stroke="#fff" stroke-width=".8"/><path d="M3.3 2.8 L4.2 2.6 L4.7 3.9 L4.1 4.4 Q4.7 5.6 5.7 6 L6.2 5.4 L7.4 5.9 L7.2 6.8 Q4 7 3.3 2.8 Z" fill="#fff"/></svg></div>
    <div class="line">marissa@marissadhomes.com<svg class="icon" viewBox="0 0 10 10"><circle cx="5" cy="5" r="4.4" fill="none" stroke="#fff" stroke-width=".8"/><rect x="2.7" y="3.4" width="4.6" height="3.2" fill="none" stroke="#fff" stroke-width=".6"/><path d="M2.7 3.4 L5 5.2 L7.3 3.4" fill="none" stroke="#fff" stroke-width=".6"/></svg></div>
    <div class="line">www.marissadhomes.com<svg class="icon" viewBox="0 0 10 10"><circle cx="5" cy="5" r="4.4" fill="none" stroke="#fff" stroke-width=".8"/><ellipse cx="5" cy="5" rx="1.8" ry="3.2" fill="none" stroke="#fff" stroke-width=".6"/><line x1="1.8" y1="5" x2="8.2" y2="5" stroke="#fff" stroke-width=".6"/></svg></div>
  </div>

  <div class="brand-standin inner-brand">SUMMIT REALTY</div>

  <div class="column middle">
    <h3 class="section-title">My Core Tenet</h3>
    <p class="tenet-lead">It’s All About YOU!</p>
    <p>My #1 priority is understanding YOUR needs and YOUR objectives.</p>
    <p>This understanding, along with working diligently on your behalf, means we accomplish your goal whether you’re purchasing your 1st home or selling a home you’ve loved so you can move on to the next chapter of your life.</p>
    <h3 class="section-title spaced">Real Estate Services &amp; Beyond…</h3>
    <p>Simply put, I help people who are local, relocating and investing, sell and purchase homes in Southern California. For purchases outside of California, I can refer to a network of agents across the country.</p>
    <p>I also provide a team who is dedicated to providing outstanding customer service throughout the transaction. My team includes a network of lenders, title, and escrow officers, in house CPA, stagers, photographers, contractors and more.</p>
  </div>

  <div class="column right">
    <h3 class="section-title">Selling Your Home</h3>
    <p>Selling your home is not like any other business transaction. It’s also personal. My priority as your Listing Agent is to guide you through what can be a complicated and sometimes emotional process.</p>
    <p>I place great emphasis on marketing your property with professional photographs, along with harnessing the power of the Internet and the virtual world to reach as many buyers as possible. Your property will be marketed to the public as well as to other agents, thus creating maximum exposure of your home.</p>
    <p>When we first meet to discuss selling your home, it’s essential for me to gain an understanding of your unique needs such as timelines, expectations and financial considerations, just to name a few. From there, I begin the process of listing and marketing your home. I lead you through negotiations and more paperwork than you ever care to do, guiding you to the successful closing of your home.</p>
    <h3 class="section-title spaced">Buying a Home</h3>
    <p>If you’re thinking about buying a home, it’s imperative you have an accomplished, real estate professional by your side to walk you through what is likely the largest purchase of your life.</p>
    <p>To get started, I like to meet with you so we have an opportunity to get to know each other as purchasing a home is a uniquely, personal endeavor. At that time, we can discuss your goals and if it’s a good time for you to purchase a home.</p>
    <p>From there, the first step is to obtain a pre-approval from a lender. I’m able to recommend various lenders who can introduce and explain the various loan products available. After you’ve been pre-approved, that’s when the fun starts! I guide you through the home buying adventure every step of the way and look forward to handing you the keys to your new home.</p>
  </div>

  <blockquote class="testimonial one"><span class="mark">“</span>Marissa got us an amazing deal on our new home and sold our old home in a week. Marissa is patient, hardworking, professional and most importantly HONEST. Marissa is definitely one of the best in the business!<br>- Paula &amp; Aaron Lind</blockquote>
  <blockquote class="testimonial two"><span class="mark">“</span>Marissa is the kind of Real Estate professional everyone wants to represent them. She is knowledgeable, ethical, energetic, and follows up on every detail. We were lucky to find her!<br>- Henry &amp; Kate Morrow</blockquote>
  <blockquote class="testimonial three"><span class="mark">“</span>During the home buying process, Marissa becomes your trusted advisor, mentor and friend. Marissa is unequivocally the reason why I was able to purchase my home in Laguna Niguel and provide my family with a world-class community.<br>- Yara Castell</blockquote>
</section>

</body>
</html>
```